Residential Remodeling Contractor needs updated business card

I need a new design for my business card.
Name of the company is Ridgefell Construction. I need a card that commands presence, strength, integrity. I have been in business for 28 years. I am a Residential Remodeling Contractor that covers all aspects of a residential remodel and build.

```html
<!DOCTYPE html>
<html lang="en">
<head>
<meta charset="utf-8">
<title>Ridgefell Construction – Business Card</title>
<link href="https://fonts.googleapis.com/css2?family=Noto+Serif:wght@700&family=Arimo:wght@400&display=swap" rel="stylesheet">
<style>
  :root {
    --backdrop: #999999;
    --navy: #183c79;
    --card-white: #ffffff;
    --ink: #333333;
  }
  * { margin: 0; padding: 0; box-sizing: border-box; }
  html, body { width: 1200px; height: 1059px; overflow: hidden; }
  body { background: var(--backdrop); position: relative; font-family: "Arimo", Arial, sans-serif; }

  .card { position: absolute; border-radius: 24px; }

  .card-front { left: 256px; top: 89px; width: 687px; height: 390px; background: var(--card-white); }
  .card-back { left: 253px; top: 569px; width: 694px; height: 394px; background: var(--navy); }

  .identity { position: absolute; right: 369px; top: 170px; text-align: right; }
  .identity-name { font-family: "Noto Serif", Georgia, serif; font-weight: 700; font-size: 26px; color: var(--navy); line-height: 1.1; letter-spacing: 0.2px; }
  .identity-role { font-size: 16.5px; color: var(--ink); margin-top: 2px; }

  .divider { position: absolute; left: 344px; top: 137px; width: 1px; height: 114px; background: var(--navy); }

  .contact { position: absolute; left: 368px; top: 128px; color: var(--ink); font-size: 16px; line-height: 1.4; }
  .contact-address { margin-bottom: 12px; }
  .contact-row { display: flex; align-items: center; gap: 7px; margin-bottom: 4px; }
  .contact-icon { width: 12px; height: 12px; flex: none; fill: var(--navy); }

  .brand { position: absolute; left: 0; right: 0; top: 172px; display: flex; justify-content: center; align-items: center; gap: 16px; }
  .brand-mark { width: 22px; height: 22px; background: var(--card-white); flex: none; }
  .brand-name { font-family: "Arimo", Arial, sans-serif; font-weight: 400; font-size: 40px; line-height: 1; color: var(--card-white); }
</style>
</head>
<body>
  <section class="card card-front">
    <div class="identity">
      <div class="identity-name">DALE HARTWELL</div>
      <div class="identity-role">Owner &amp; Manager</div>
    </div>
    <div class="divider"></div>
    <div class="contact">
      <div class="contact-address">P.O. Box&nbsp; Street Name<br>Country Name AB, A5B 521</div>
      <div class="contact-row">
        <svg class="contact-icon" viewBox="0 0 12 12"><path d="M1 4c0-2 10-2 10 0v1H8.5V3.8h-5V5H1zM3 6h6l1.5 5h-9z"/></svg>
        <span>555 214 7380</span>
      </div>
      <div class="contact-row">
        <svg class="contact-icon" viewBox="0 0 12 12"><path d="M1 5l5-4 5 4v6H1zM2 6v4.2l3-2.2zM10 6l-3 2 3 2.2zM2.6 10.5h6.8L6 8z"/></svg>
        <span>info@ridgefellconstruction.com</span>
      </div>
      <div class="contact-row">
        <svg class="contact-icon" viewBox="0 0 12 12"><circle cx="6" cy="6" r="5.5"/><path d="M3 3.5l2 1-0.5 2 1.5 1-1 2.5M8 2.5l-0.5 2 2 1" stroke="#fff" stroke-width="1" fill="none"/></svg>
        <span>www.ridgefellconstruction.com</span>
      </div>
    </div>
  </section>

  <section class="card card-back">
    <div class="brand">
      <span class="brand-mark"></span>
      <span class="brand-name">Ridgefell Construction</span>
    </div>
  </section>
</body>
</html>
```